Business Card & Letterhead Design

We a financial advice company based in Australia. We provide advice to wealthy farmers.

We are changing our business name FROM Brightvale Financial TO Tallowmere Wealth and we need a new letterhead and double sided business card design

Attached is designs from our previous branding (Brightvale Financial) as it includes all the details we require on the new Tallowmere Wealth business cards and letterhead.

Need extra days to review

```html
<!DOCTYPE html>
<html lang="en">
<head>
<meta charset="utf-8">
<title>Tallowmere Wealth – Stationery</title>
<link rel="stylesheet" href="https://fonts.googleapis.com/css2?family=Cinzel:wght@400;700&family=Roboto:wght@400;500&family=Tinos:wght@700&display=swap">
<style>
:root{
  --backdrop:#999999;
  --charcoal:#3d3d3d;
  --slate:#6b6b6b;
  --paper:#f7f7f5;
  --ghost:#ececea;
  --ink:#3a3a3a;
  --white:#ffffff;
}
*{margin:0;padding:0;box-sizing:border-box}
html,body{width:1200px;height:1032px;overflow:hidden;background:var(--backdrop)}
.canvas{position:relative;width:1200px;height:1032px;font-family:"Roboto",sans-serif}
.abs{position:absolute}
svg{display:block}

/* business card front */
.card{position:absolute;width:271px;height:164px;overflow:hidden}
.card-front{left:127px;top:330px;background:var(--charcoal)}
.card-front .brand-name{left:0;width:271px;top:94px;text-align:center;color:var(--white);font-family:"Cinzel",serif;font-size:13.5px;letter-spacing:.4px;white-space:nowrap}
.card-front .tagline{left:0;width:271px;top:110px;text-align:center;color:#d8d8d8;font-family:"Roboto",sans-serif;font-size:5.8px;letter-spacing:2.2px;white-space:nowrap}

/* business card back */
.card-back{left:127px;top:537px;background:var(--white)}
.card-back .brand-name{left:76px;top:23px;color:var(--ink);font-family:"Cinzel",serif;font-size:13px;letter-spacing:.3px;white-space:nowrap}
.card-back .tagline{left:80px;top:38px;color:#777;font-size:5.6px;letter-spacing:2px;white-space:nowrap}
.person-name{left:31px;top:91px;color:var(--white);font-family:"Tinos",serif;font-weight:700;font-size:8.5px}
.person-role{left:31px;top:103px;color:#e0e0e0;font-size:5.6px;line-height:7.4px}
.card-line{color:#e6e6e6;font-size:5.6px;line-height:7.2px;white-space:nowrap}
.card-icon{width:5px;height:5px}

/* letterhead */
.letterhead{position:absolute;left:447px;top:74px;width:625px;height:884px;background:var(--paper);overflow:hidden}
.letterhead .brand-name{left:0;width:320px;top:120px;text-align:center;color:var(--ink);font-family:"Cinzel",serif;font-size:17.5px;letter-spacing:.5px;white-space:nowrap}
.letterhead .tagline{left:0;width:320px;top:141px;text-align:center;color:#666;font-size:7.4px;letter-spacing:2.6px;white-space:nowrap}
.lh-contact{color:var(--ink);font-size:10px;line-height:14.5px;white-space:nowrap}
.lh-icon{width:9px;height:9px}
.lh-address{left:346px;width:200px;top:832px;text-align:center;color:var(--white);font-size:9.8px;line-height:14.5px}
</style>
</head>
<body>
<main class="canvas">

  <!-- Business card: front -->
  <section class="card card-front" aria-label="Business card front">
    <svg class="abs" style="left:0;top:0" width="271" height="164" viewBox="0 0 271 164">
      <circle cx="209" cy="70" r="76" fill="none" stroke="#4a4a4a" stroke-width="3"/>
      <circle cx="136" cy="67" r="21" fill="none" stroke="var(--white)" stroke-width="1.8"/>
    </svg>
    <div class="abs brand-name">TALLOWMERE WEALTH</div>
    <div class="abs tagline">STRATEGIC FINANCIAL ADVICE</div>
  </section>

  <!-- Business card: back -->
  <section class="card card-back" aria-label="Business card back">
    <svg class="abs" style="left:0;top:0" width="271" height="164" viewBox="0 0 271 164">
      <circle cx="46" cy="34" r="17" fill="none" stroke="var(--ink)" stroke-width="1.5"/>
      <path d="M0,66 C80,74 170,62 271,44 L271,48 C170,66 80,78 0,70 Z" fill="var(--slate)"/>
      <path d="M0,74 C80,82 170,70 271,52 L271,164 L0,164 Z" fill="var(--charcoal)"/>
    </svg>
    <div class="abs brand-name">TALLOWMERE WEALTH</div>
    <div class="abs tagline">STRATEGIC FINANCIAL ADVICE</div>

    <div class="abs person-name">SAM HARTLEY</div>
    <div class="abs person-role">B.Com. Adv Dip Fin Plan<br>Managing Director</div>

    <svg class="abs card-icon" style="left:32px;top:130px" viewBox="0 0 10 10"><rect x="1" y="2" width="8" height="6" fill="#ddd"/><path d="M1,2 L5,6 L9,2" stroke="#3d3d3d" fill="none"/></svg>
    <div class="abs card-line" style="left:43px;top:128px">sam@brightvalefinancial.com.au</div>
    <svg class="abs card-icon" style="left:32px;top:138px" viewBox="0 0 10 10"><circle cx="5" cy="5" r="4" fill="#ddd"/></svg>
    <div class="abs card-line" style="left:43px;top:136px">www.brightvalefinancial.com.au</div>

    <svg class="abs card-icon" style="left:153px;top:91px" viewBox="0 0 10 10"><path d="M1,4 Q5,0 9,4 L8,6 L6,5 L4,5 L2,6 Z M3,6 H7 V9 H3 Z" fill="#ddd"/></svg>
    <div class="abs card-line" style="left:165px;top:89px">(07) 3210 5864</div>
    <svg class="abs card-icon" style="left:153px;top:100px" viewBox="0 0 10 10"><rect x="3" y="1" width="4.5" height="8" rx="1" fill="#ddd"/></svg>
    <div class="abs card-line" style="left:165px;top:98px">(07) 3158 2406</div>
    <svg class="abs card-icon" style="left:153px;top:108px" viewBox="0 0 10 10"><rect x="1" y="3" width="8" height="4" fill="#ddd"/><rect x="3" y="1" width="4" height="2" fill="#ddd"/><rect x="3" y="7" width="4" height="2" fill="#ddd"/></svg>
    <div class="abs card-line" style="left:165px;top:106px">0412 586 330</div>
    <svg class="abs card-icon" style="left:153px;top:117px" viewBox="0 0 10 10"><path d="M5,9 L2,5 A3,3 0 1 1 8,5 Z" fill="#ddd"/><circle cx="5" cy="4" r="1" fill="#3d3d3d"/></svg>
    <div class="abs card-line" style="left:165px;top:115px">Suite 4C, 18 Morrow St<br>Ridgeford QLD 4170</div>
    <svg class="abs card-icon" style="left:153px;top:135px" viewBox="0 0 10 10"><path d="M5,9 L2,5 A3,3 0 1 1 8,5 Z" fill="#ddd"/><circle cx="5" cy="4" r="1" fill="#3d3d3d"/></svg>
    <div class="abs card-line" style="left:165px;top:133px">PO Box 5120<br>Ridgeford QLD 4170</div>
  </section>

  <!-- Letterhead -->
  <section class="letterhead" aria-label="Letterhead">
    <svg class="abs" style="left:0;top:0" width="625" height="884" viewBox="0 0 625 884">
      <path d="M50,0 L625,0 L625,30 C500,14 300,4 50,0 Z" fill="var(--charcoal)"/>
      <path d="M190,10 C350,14 500,24 625,38 L625,46 C500,30 350,18 190,10 Z" fill="var(--slate)"/>
      <circle cx="313" cy="512" r="197" fill="none" stroke="var(--ghost)" stroke-width="4"/>
      <circle cx="159" cy="82" r="33" fill="none" stroke="var(--ink)" stroke-width="2.2"/>
      <path d="M0,800 C40,830 110,848 200,845 C330,840 420,790 560,792 C590,793 610,800 625,806 L625,812 C560,796 430,800 300,835 C200,860 80,858 0,832 Z" fill="var(--slate)"/>
      <path d="M0,840 C100,870 220,860 320,832 C430,802 540,800 625,820 L625,884 L0,884 Z" fill="var(--charcoal)"/>
      <path d="M0,848 C100,878 220,868 310,843" fill="none" stroke="var(--white)" stroke-width="3"/>
      <path d="M0,858 C100,884 220,876 300,854" fill="none" stroke="var(--slate)" stroke-width="4"/>
    </svg>
    <div class="abs brand-name">TALLOWMERE WEALTH</div>
    <div class="abs tagline">STRATEGIC FINANCIAL ADVICE</div>

    <svg class="abs lh-icon" style="left:50px;top:758px" viewBox="0 0 10 10"><path d="M1,4 Q5,0 9,4 L8,6 L6,5 L4,5 L2,6 Z M3,6 H7 V9 H3 Z" fill="var(--ink)"/></svg>
    <div class="abs lh-contact" style="left:70px;top:754px">(07) 3210 5864</div>
    <svg class="abs lh-icon" style="left:50px;top:772px" viewBox="0 0 10 10"><rect x="2.5" y="0.5" width="5" height="9" rx="1" fill="var(--ink)"/></svg>
    <div class="abs lh-contact" style="left:70px;top:768px">(07) 3158 2406</div>
    <svg class="abs lh-icon" style="left:50px;top:787px" viewBox="0 0 10 10"><rect x="1" y="3" width="8" height="4" fill="var(--ink)"/><rect x="3" y="1" width="4" height="2" fill="var(--ink)"/><rect x="3" y="7" width="4" height="2" fill="var(--ink)"/></svg>
    <div class="abs lh-contact" style="left:70px;top:783px">0412 586 330</div>

    <svg class="abs lh-icon" style="left:168px;top:772px" viewBox="0 0 10 10"><rect x="1" y="2" width="8" height="6" fill="var(--ink)"/><path d="M1,2 L5,6 L9,2" stroke="var(--paper)" fill="none"/></svg>
    <div class="abs lh-contact" style="left:184px;top:768px">sam@brightvalefinancial.com.au</div>
    <svg class="abs lh-icon" style="left:168px;top:787px" viewBox="0 0 10 10"><circle cx="5" cy="5" r="4" fill="var(--ink)"/></svg>
    <div class="abs lh-contact" style="left:184px;top:783px">www.brightvalefinancial.com.au</div>

    <div class="abs lh-address">PO Box 5120 Ridgeford QLD 4170<br>Suite 4C, 18 Morrow St<br>Ridgeford QLD 4170</div>
  </section>

</main>
</body>
</html>
```